2023 Cheers to 50 Years Graphic

Hi - I'd like a high-res image that's also print ready that we can use around our office with our 2023 slogan: Cheers to 50 years!

Ideally we'd like a catchy image, the slogan and our logo.

I'll attach the 2022 example. Please use our 50th anniversary logo also attached.

Graphic could be anything celebratory!

Main demographic is males.

Maybe cheers of champagne glasses or beer. But open top option that does not involve alcohol too.

```html
<!DOCTYPE html>
<html lang="en">
<head>
<meta charset="utf-8">
<title>Cheers to 50 Years</title>
<link rel="stylesheet" href="https://fonts.googleapis.com/css2?family=Lobster+Two:ital,wght@0,700;1,700&display=swap">
<style>
  :root {
    --navy: #2d3a80;
    --glow: #ffffff;
    --spark-core: #fffdf2;
    --spark-light: #ffe7a8;
    --spark-gold: #f2a93a;
    --ember: #c46f1a;
    --bokeh: #f7c23c;
    --night: #2a1405;
  }
  html, body {
    margin: 0;
    padding: 0;
    width: 1200px;
    height: 815px;
    overflow: hidden;
    background: var(--night);
  }
  .poster {
    position: relative;
    width: 1200px;
    height: 815px;
    overflow: hidden;
    font-family: "Lobster Two", "Lobster", cursive;
  }
  .sparkler-photo {
    position: absolute;
    inset: 0;
    background:
      radial-gradient(ellipse 420px 150px at 610px 400px, var(--spark-core) 0%, rgba(255,253,242,0.95) 40%, rgba(255,231,168,0) 100%),
      radial-gradient(ellipse 640px 330px at 610px 400px, var(--spark-light) 0%, rgba(242,169,58,0.9) 45%, rgba(196,111,26,0) 100%),
      radial-gradient(circle 95px at 105px 185px, rgba(247,194,60,0.85) 0%, rgba(247,194,60,0.6) 70%, rgba(247,194,60,0) 100%),
      radial-gradient(circle 80px at 150px 620px, rgba(247,194,60,0.8) 0%, rgba(247,194,60,0.55) 70%, rgba(247,194,60,0) 100%),
      radial-gradient(circle 60px at 160px 790px, rgba(247,194,60,0.7) 0%, rgba(247,194,60,0) 100%),
      radial-gradient(circle 75px at 1160px 100px, rgba(250,190,100,0.85) 0%, rgba(250,190,100,0.55) 70%, rgba(250,190,100,0) 100%),
      radial-gradient(circle 70px at 30px 30px, rgba(240,160,70,0.7) 0%, rgba(240,160,70,0) 100%),
      radial-gradient(ellipse 900px 620px at 600px 420px, var(--spark-gold) 0%, var(--ember) 40%, rgba(110,55,14,0.95) 72%, var(--night) 100%),
      var(--night);
  }
  .brand-halo {
    position: absolute;
    left: 836px;
    top: 596px;
    width: 280px;
    height: 172px;
    border-radius: 50%;
    background: radial-gradient(ellipse at center, rgba(255,255,255,0.97) 0%, rgba(255,255,255,0.85) 55%, rgba(255,255,255,0) 75%);
  }
  .headline {
    position: absolute;
    margin: 0;
    text-align: center;
    color: var(--navy);
    font-weight: 700;
    line-height: 1;
    white-space: nowrap;
    text-shadow: 0 0 14px var(--glow), 0 0 28px var(--glow), 0 0 40px rgba(255,255,255,0.8);
  }
  .headline-year {
    left: 0;
    width: 1126px;
    top: 138px;
    font-style: normal;
    font-size: 134px;
  }
  .headline-slogan {
    left: 0;
    width: 1180px;
    top: 296px;
    font-style: italic;
    font-size: 129px;
  }
  .brand-name {
    position: absolute;
    left: 851px;
    top: 668px;
    width: 250px;
    margin: 0;
    text-align: center;
    color: var(--navy);
    font-weight: 700;
    font-style: normal;
    font-size: 26px;
    line-height: 1;
    white-space: nowrap;
  }
</style>
</head>
<body>
  <main class="poster">
    <div class="sparkler-photo" role="img" aria-label="Close-up photo of a lit sparkler bursting with bright golden sparks against a dark background with warm bokeh lights"></div>
    <div class="brand-halo"></div>
    <h1 class="headline headline-year">2023</h1>
    <p class="headline headline-slogan">Cheers to 50 years!</p>
    <p class="brand-name">Harborline Supply</p>
  </main>
</body>
</html>
```